New B2C website design to help dads be better dads

DadHarbor is a website to help dads be the “best dad you can be.”

We require our website to be designed into a PSD format, no coding necessary.

The general concept is a two-page design. The first page is the login page, the second page is the home page. Once at the home page, rather than navigating to and from different pages, the user will push and pull through different visual and functional layers of the hierarchy. In theory, this should add to the user experience by having a visual anchor of where they are (through layered pagination) as well as improving loading times since the new information should only be a delta in data load versus a brand new page load.

The general look-and-feel we are going for is clean, simple, minimal. This means that the winning design will show us a good eye for web-optimized typography, good use of white (negative) space, and good use of a visually pleasing grid.

We require a total of 6 page "views" plus the landing page. We note that many of the views are similar to one another.
Landing page
Milestone view
Task view
Content view, articles
Content view, products
Search view
What's new view

Please review all of the additional information provided as well as the attachments for examples.

We provide the following websites as good references for:

Typography:
http://example-kelvorn.com/journal/

Use of white space:
http://www.trenvaskit.com/
http://moldrefin.com/

Example for “scrolling” page concept as well as good balance of color, typography, and white space:
http://www.qorbitalmeet.eu/

Please contact us with questions so that we can guide your design effort.
Updates

Hello designers,

The following information is added to help guide the design process:

1.  For the text dialogue below the landing page, please assume the following word count:
"why are we making dad harbor?": 250 words
"who are we?" 200 words
"what's the deal with the penguin logo?" 300 words

For the social media links, please see http://www.gravelplumbs.com/
Notice the floating "social" bar that is always to the right.  This is the concept we are going for, please try to implement this as you see fit. 

Target Market(s)

Fathers of young children ages 0-6 years old.

Industry/Entity Type

Product

Font styles to use
Sans Serif

Requirements
Must have
• Clean lines, minimal design concept

Incorporation of our logo (see attached document)

Header content is static for all views after landing page, see example

This page WILL be responsive, please keep that in mind when designing
The timeline bar should be to the left, with the timeline bar’s “milestones” also being responsive.

Designer is free to suggest font types, but any fonts used must be royalty-free and web-optimized. We request a minimum number of font types as well as fonts that load relatively fast. We reinforce that visually appealing typography is a significant factor in the winning design choice.

While we are not expecting the winning design to include code, please keep in mind that the final implementation needs to be optimized for desktop, tablet, and mobile platforms.

If you are using stock photography that is not generated by you, please provide where/how we can obtain imagery, as well as price.

All custom graphics must be available in original formats; Photoshop/GIMP layered files for layout design, and vector formats for logos, icons and other graphical elements.

Please incorporate “Blue” into design elements as you see fit, as the RGB 67 74 169 Blue is the primary color used in our brand. The complement to this blue is 255 202 0, a brownish orange. Feel free to use this color as well, although please keep it to a lesser amount.

Background color is your choice, do not feel the need to use the grey.
Should not have
• Excessive graphical content such that it affects loading times

Excessive use of too many font types such that it affects loading times

```html
<!DOCTYPE html>
<html lang="en">
<head>
<meta charset="utf-8">
<title>DadHarbor – Home</title>
<link href="https://fonts.googleapis.com/css2?family=PT+Sans:wght@400;700&family=Rokkitt:wght@300;400&display=swap" rel="stylesheet">
<style>
:root{
  --brand-blue:#434aa9;
  --brand-blue-dark:#3a3f9c;
  --accent-yellow:#ffca00;
  --accent-orange:#e09a12;
  --page-bg:#f7f7f7;
  --header-bg:#ffffff;
  --rule:#dcdcdc;
  --text:#444;
  --muted:#777;
  --star:#ffc400;
}
*{box-sizing:border-box;margin:0;padding:0}
html,body{width:938px;height:1200px;overflow:hidden}
body{background:var(--page-bg);font-family:"PT Sans",sans-serif;color:var(--text);position:relative}

.site-header{position:absolute;left:0;top:0;width:938px;height:146px;background:var(--header-bg);border-bottom:1px solid var(--rule)}
.brand{position:absolute;left:77px;top:100px;display:flex;align-items:center;gap:8px;font-family:"PT Sans",sans-serif;font-weight:700;font-size:20px;color:var(--brand-blue)}
.brand-dot{width:12px;height:12px;border-radius:50%;background:var(--brand-blue)}
.welcome{position:absolute;right:79px;top:14px;font-family:"Rokkitt",serif;font-size:24px;color:var(--accent-orange);font-weight:400}
.search{position:absolute;left:551px;top:60px;display:flex;gap:7px}
.search-input{width:237px;height:27px;border:1px solid #ddd;background:#fff;font:12px "PT Sans",sans-serif;color:#999;padding:0 11px;line-height:25px}
.search-btn{width:58px;height:27px;background:var(--accent-yellow);border:1px solid #f0b400;color:#b8760a;font:12px "PT Sans",sans-serif;line-height:25px;text-align:center}
.user-bar{position:absolute;left:550px;top:109px;width:304px;display:flex;align-items:center;font-size:12px}
.score{color:var(--brand-blue);display:flex;align-items:center;gap:7px;font-size:13px}
.account-links{margin-left:auto;color:var(--muted)}
.account-links span{margin:0 6px;color:#aaa}

.timeline-line{position:absolute;left:77px;top:162px;width:1px;height:1002px;background:#c8c8c8}
.timeline-arrow{position:absolute;left:73px;width:9px;height:6px}
.milestone{position:absolute;left:46px;display:flex;align-items:center}
.milestone-age{width:26px;font-size:10px;color:#888;text-align:right;margin-right:6px}
.milestone-dot{width:13px;height:13px;border-radius:50%;background:#555;display:flex;align-items:center;justify-content:center}
.milestone-title{margin-left:12px;font-family:"Rokkitt",serif;font-size:19px;color:#666}

.sort{position:absolute;left:709px;top:172px;display:flex;align-items:center;gap:8px;font-size:10px;color:#777}
.sort-select{width:107px;height:22px;border:1px solid #ccc;background:#fff;font-size:10px;color:#444;padding:0 8px;display:flex;align-items:center;justify-content:space-between}
.section-rule{position:absolute;left:78px;top:222px;width:782px;height:1px;background:#cfcfcf}

.task-list{position:absolute;left:103px;top:222px;width:189px;height:285px;background:#fff;border:1px solid #d8d8d8;border-top:none;padding:0 7px;list-style:none}
.task-list li{height:34.2px;border-bottom:1px solid #e6e6e6;display:flex;align-items:center;gap:9px;font-size:12px;color:#444;padding-left:12px}
.task-list li:last-child{border-bottom:none}
.checkbox{width:9px;height:9px;border:1px solid #999;background:#eee;position:relative}

.card-grid{position:absolute;left:307px;top:245px;display:grid;grid-template-columns:263px 263px;grid-auto-rows:293px;column-gap:24px;row-gap:25px}
.card{background:#fff;border:1px solid #d8d8d8;padding:5px;position:relative}
.card-photo{height:143px;position:relative}
.card-badge{position:absolute;right:2px;bottom:2px;width:31px;height:31px;background:var(--accent-yellow);display:flex;align-items:center;justify-content:center}
.card-title{margin:14px 8px 0;font-family:"Rokkitt",serif;font-size:14.5px;line-height:18px;color:var(--brand-blue);font-weight:400}
.rating{margin:7px 8px 0;display:flex;align-items:center;gap:2px;font-size:11px;color:#666}
.rating .count{margin-left:9px}
.card-text{margin:10px 8px 0;font-size:11px;line-height:18px;color:#666}
.read-more{color:var(--brand-blue);white-space:nowrap}
.read-more svg{vertical-align:-1px;margin:0 3px 0 4px}

.social-bar{position:absolute;left:896px;top:548px;width:42px;height:167px;background:#4a4fb0;display:flex;flex-direction:column;align-items:center;justify-content:space-around;padding:8px 0}
.social-dot{width:18px;height:18px;border-radius:50%;background:#fff}
</style>
</head>
<body>

<header class="site-header">
  <div class="brand"><span class="brand-dot"></span>DadHarbor</div>
  <h1 class="welcome">Welcome Greg, what would you like to do today?</h1>
  <div class="search">
    <div class="search-input">Keyword...</div>
    <div class="search-btn">SEARCH</div>
  </div>
  <div class="user-bar">
    <div class="score">
      <svg width="10" height="9" viewBox="0 0 10 9"><path d="M5 9 L0.8 4.6 A2.4 2.4 0 0 1 5 1.6 A2.4 2.4 0 0 1 9.2 4.6 Z" fill="#434aa9"/></svg>
      Super Dad Score: 10,500
    </div>
    <div class="account-links">My Account<span>|</span>Log out</div>
  </div>
</header>

<div class="timeline-line"></div>
<svg class="timeline-arrow" style="top:159px" viewBox="0 0 9 6"><path d="M1 5 L4.5 1 L8 5" stroke="#aaa" fill="none"/></svg>
<svg class="timeline-arrow" style="top:1161px" viewBox="0 0 9 6"><path d="M1 1 L4.5 5 L8 1" stroke="#aaa" fill="none"/></svg>

<div class="milestone" style="top:175px">
  <span class="milestone-age">-3 mo</span>
  <span class="milestone-dot"><svg width="9" height="7" viewBox="0 0 9 7"><path d="M4 0.5 L1 3.5 L4 6.5 M1 3.5 H8" stroke="#fff" stroke-width="1.6" fill="none"/></svg></span>
  <span class="milestone-title">Prepare for the baby arrival</span>
</div>
<div class="milestone" style="top:551px">
  <span class="milestone-age">0 mo</span>
  <span class="milestone-dot"><svg width="9" height="7" viewBox="0 0 9 7"><path d="M5 0.5 L8 3.5 L5 6.5 M8 3.5 H1" stroke="#fff" stroke-width="1.6" fill="none"/></svg></span>
  <span class="milestone-title">What’s the Latest?</span>
</div>
<div class="milestone" style="top:609px">
  <span class="milestone-age">0 mo</span>
  <span class="milestone-dot"><svg width="9" height="7" viewBox="0 0 9 7"><path d="M5 0.5 L8 3.5 L5 6.5 M8 3.5 H1" stroke="#fff" stroke-width="1.6" fill="none"/></svg></span>
  <span class="milestone-title">What you searched for</span>
</div>

<div class="sort">
  <span>Sort by :</span>
  <div class="sort-select">Most recent<svg width="7" height="4" viewBox="0 0 7 4"><path d="M0 0 H7 L3.5 4Z" fill="#555"/></svg></div>
</div>
<div class="section-rule"></div>

<ul class="task-list">
  <li><span class="checkbox"></span>Buy a crib</li>
  <li><span class="checkbox"></span>Assemble the crib</li>
  <li><span class="checkbox"></span>Buy a stroller</li>
  <li><span class="checkbox"><svg width="9" height="9" viewBox="0 0 9 9" style="position:absolute;left:-1px;top:-1px"><path d="M2 4.5 L4 6.5 L7.5 2" stroke="#434aa9" stroke-width="1.4" fill="none"/></svg></span>Buy a carseat</li>
  <li><span class="checkbox"></span>Install a carseat</li>
  <li><span class="checkbox"></span>Learn to change a diaper</li>
  <li><span class="checkbox"></span>Learn to hold a baby</li>
  <li><span class="checkbox"></span>Set a fedding schedule</li>
</ul>

<svg width="0" height="0" style="position:absolute">
  <defs>
    <symbol id="star" viewBox="0 0 16 16"><polygon points="8,0.8 10.2,5.6 15.4,6.1 11.5,9.6 12.6,14.8 8,12.1 3.4,14.8 4.5,9.6 0.6,6.1 5.8,5.6" fill="#ffc400"/></symbol>
    <symbol id="star-half" viewBox="0 0 16 16"><polygon points="8,0.8 10.2,5.6 15.4,6.1 11.5,9.6 12.6,14.8 8,12.1 3.4,14.8 4.5,9.6 0.6,6.1 5.8,5.6" fill="none" stroke="#ffc400" stroke-width="1.3"/><polygon points="8,0.8 8,12.1 3.4,14.8 4.5,9.6 0.6,6.1 5.8,5.6" fill="#ffc400"/></symbol>
    <symbol id="doc-icon" viewBox="0 0 18 20"><path d="M1 1 H17 V14 L12 19 H1 Z" fill="#111"/><path d="M12 19 V14 H17" fill="#555"/></symbol>
    <symbol id="cart-icon" viewBox="0 0 22 18"><path d="M1 2 H4 L7 12 H18 L20 5 H5" stroke="#111" stroke-width="1.8" fill="none"/><path d="M8 8 H19 M11 5 V12 M15 5 V12" stroke="#111" stroke-width="1"/><circle cx="8" cy="15.5" r="1.6" fill="#111"/><circle cx="17" cy="15.5" r="1.6" fill="#111"/></symbol>
    <symbol id="plus-circle" viewBox="0 0 10 10"><circle cx="5" cy="5" r="5" fill="#434aa9"/><path d="M5 2.5 V7.5 M2.5 5 H7.5" stroke="#fff" stroke-width="1.4"/></symbol>
  </defs>
</svg>

<main class="card-grid">
  <article class="card">
    <div class="card-photo" role="img" aria-label="Photo of a baby in a car seat holding a colourful toy" style="background:linear-gradient(135deg,#5a5a5e,#a9a3a0 45%,#2b2b2e)">
      <span class="card-badge"><svg width="17" height="19"><use href="#doc-icon"/></svg></span>
    </div>
    <h2 class="card-title">Pellentesque habitant morbi tristique senectus et netus</h2>
    <div class="rating"><svg width="16" height="16"><use href="#star"/></svg><svg width="16" height="16"><use href="#star"/></svg><svg width="16" height="16"><use href="#star"/></svg><svg width="16" height="16"><use href="#star"/></svg><svg width="16" height="16"><use href="#star-half"/></svg><span class="count">3,121 ratings</span></div>
    <p class="card-text">I went out to buy my first car seat and had to earn my PhD in car seats, Newtonian physics, and anti-stain technology··· <span class="read-more"><svg width="10" height="10"><use href="#plus-circle"/></svg>Read More</span></p>
  </article>
  <article class="card">
    <div class="card-photo" role="img" aria-label="Photo of a smiling baby in a brown car seat" style="background:linear-gradient(135deg,#7a6a58,#c9b9a6 50%,#4b3e33)">
      <span class="card-badge"><svg width="22" height="18"><use href="#cart-icon"/></svg></span>
    </div>
    <h2 class="card-title">Pellentesque habitant morbi tristique senectus et netus</h2>
    <div class="rating"><svg width="16" height="16"><use href="#star"/></svg><svg width="16" height="16"><use href="#star"/></svg><svg width="16" height="16"><use href="#star"/></svg><svg width="16" height="16"><use href="#star"/></svg><svg width="16" height="16"><use href="#star-half"/></svg><span class="count">3,121 ratings</span></div>
    <p class="card-text">I went out to buy my first car seat and had to earn my PhD in car seats, Newtonian physics, and anti-stain technology··· <span class="read-more"><svg width="10" height="10"><use href="#plus-circle"/></svg>Read More</span></p>
  </article>
  <article class="card">
    <div class="card-photo" role="img" aria-label="Photo of a toddler in a red car seat" style="background:linear-gradient(135deg,#8a7358,#d8c3a2 45%,#a33a2c)">
      <span class="card-badge"><svg width="17" height="19"><use href="#doc-icon"/></svg></span>
    </div>
    <h2 class="card-title">Pellentesque habitant morbi tristique senectus et netus</h2>
    <div class="rating"><svg width="16" height="16"><use href="#star"/></svg><svg width="16" height="16"><use href="#star"/></svg><svg width="16" height="16"><use href="#star"/></svg><svg width="16" height="16"><use href="#star"/></svg><svg width="16" height="16"><use href="#star-half"/></svg><span class="count">3,121 ratings</span></div>
    <p class="card-text">I went out to buy my first car seat and had to earn my PhD in car seats, Newtonian physics, and anti-stain technology··· <span class="read-more"><svg width="10" height="10"><use href="#plus-circle"/></svg>Read More</span></p>
  </article>
  <article class="card">
    <div class="card-photo" role="img" aria-label="Photo of a baby strapped into a dark grey infant seat" style="background:linear-gradient(180deg,#4a4c52,#6b6e76 50%,#3a3c40)">
      <span class="card-badge"><svg width="22" height="18"><use href="#cart-icon"/></svg></span>
    </div>
    <h2 class="card-title">Pellentesque habitant morbi tristique senectus et netus</h2>
    <div class="rating"><svg width="16" height="16"><use href="#star"/></svg><svg width="16" height="16"><use href="#star"/></svg><svg width="16" height="16"><use href="#star"/></svg><svg width="16" height="16"><use href="#star"/></svg><svg width="16" height="16"><use href="#star-half"/></svg><span class="count">3,121 ratings</span></div>
    <p class="card-text">I went out to buy my first car seat and had to earn my PhD in car seats, Newtonian physics, and anti-stain technology··· <span class="read-more"><svg width="10" height="10"><use href="#plus-circle"/></svg>Read More</span></p>
  </article>
  <article class="card">
    <div class="card-photo" role="img" aria-label="Photo of a baby held by a seat belt on a grey car seat" style="background:linear-gradient(135deg,#6f7a80,#b7c0c2 50%,#5b6468)">
      <span class="card-badge"><svg width="17" height="19"><use href="#doc-icon"/></svg></span>
    </div>
    <h2 class="card-title">Pellentesque habitant morbi tristique senectus et netus</h2>
    <div class="rating"><svg width="16" height="16"><use href="#star"/></svg><svg width="16" height="16"><use href="#star"/></svg><svg width="16" height="16"><use href="#star"/></svg><svg width="16" height="16"><use href="#star"/></svg><svg width="16" height="16"><use href="#star-half"/></svg><span class="count">3,121 ratings</span></div>
    <p class="card-text">I went out to buy my first car seat and had to earn my PhD in car seats, Newtonian physics, and anti-stain technology··· <span class="read-more"><svg width="10" height="10"><use href="#plus-circle"/></svg>Read More</span></p>
  </article>
  <article class="card">
    <div class="card-photo" role="img" aria-label="Photo of a sleeping newborn in a car seat" style="background:linear-gradient(135deg,#4a3a2e,#c9b6a8 50%,#5e4c40)">
      <span class="card-badge"><svg width="22" height="18"><use href="#cart-icon"/></svg></span>
    </div>
    <h2 class="card-title">Pellentesque habitant morbi tristique senectus et netus</h2>
    <div class="rating"><svg width="16" height="16"><use href="#star"/></svg><svg width="16" height="16"><use href="#star"/></svg><svg width="16" height="16"><use href="#star"/></svg><svg width="16" height="16"><use href="#star"/></svg><svg width="16" height="16"><use href="#star-half"/></svg><span class="count">3,121 ratings</span></div>
    <p class="card-text">I went out to buy my first car seat and had to earn my PhD in car seats, Newtonian physics, and anti-stain technology··· <span class="read-more"><svg width="10" height="10"><use href="#plus-circle"/></svg>Read More</span></p>
  </article>
</main>

<nav class="social-bar" aria-label="Share">
  <span class="social-dot"></span>
  <span class="social-dot"></span>
  <span class="social-dot"></span>
  <span class="social-dot"></span>
</nav>

</body>
</html>
```